Design a New Business Card for Our Company

We are looking for fresh, unique, and a modern business card that reflects our roots as digital marketing agency focused on SEM.

Industry/Entity Type

Marketing

Contact Information for Business Card

looking for very unique out of the box designs. clean and modern that compliments our logo

Requirements
Must have
• colors should match our logo
• Front should have name, address, email, and phone/fax of the person, phone/fax are the same number
• back should have our url

```html
<!DOCTYPE html>
<html lang="en">
<head>
<meta charset="utf-8">
<title>Brightpath Media – Business Card</title>
<link rel="stylesheet" href="https://fonts.googleapis.com/css2?family=Arimo:wght@400;700&display=swap">
<style>
  :root {
    --brand-blue: #5b9bd8;
    --brand-blue-deep: #4a8ccd;
    --ink-grey: #6f6f6f;
    --soft-grey: #b4b4b4;
    --card-white: #ffffff;
    --backdrop: #e9e6e1;
  }
  * { margin: 0; padding: 0; box-sizing: border-box; }
  html, body {
    width: 1200px; height: 950px; overflow: hidden;
    background: var(--backdrop);
    font-family: "Arimo", Arial, sans-serif;
  }
  .canvas { position: relative; width: 1200px; height: 950px; }

  .card {
    position: absolute; width: 620px; height: 354px; overflow: hidden;
    box-shadow: 0 14px 30px rgba(0,0,0,0.22);
  }

  /* Back side */
  .card-back { left: 120px; top: 90px; background: var(--brand-blue); color: var(--card-white); }
  .card-back .wordmark {
    position: absolute; left: 0; right: 0; top: 118px; text-align: center;
    font-size: 58px; font-weight: 700; letter-spacing: -1px; line-height: 1;
  }
  .card-back .wordmark-sub {
    position: absolute; left: 0; right: 0; top: 180px; text-align: center;
    font-size: 15px; letter-spacing: 11px; font-weight: 400;
  }
  .card-back .url {
    position: absolute; left: 0; right: 0; bottom: 56px; text-align: center;
    font-size: 15px; letter-spacing: 5px;
  }

  /* Front side */
  .card-front { left: 460px; top: 500px; background: var(--card-white); }
  .card-front .corner-shapes { position: absolute; inset: 0; }
  .card-front .wordmark {
    position: absolute; right: 70px; top: 48px; text-align: right;
    color: var(--brand-blue); font-weight: 700; font-size: 52px; letter-spacing: -1px; line-height: 1;
  }
  .card-front .wordmark-sub {
    position: absolute; right: 62px; top: 104px;
    color: var(--brand-blue); font-weight: 700; font-size: 13px; letter-spacing: 11px;
  }
  .contact { position: absolute; left: 66px; bottom: 40px; display: flex; gap: 22px; }
  .person .name { color: var(--soft-grey); font-size: 23px; }
  .person .role { color: var(--brand-blue); font-size: 15px; margin-top: 2px; margin-bottom: 14px; }
  .details { list-style: none; color: var(--ink-grey); font-size: 15px; }
  .details li { display: flex; align-items: center; gap: 10px; height: 22px; }
  .details svg { width: 14px; height: 14px; fill: var(--ink-grey); }
  .divider { width: 2px; background: var(--brand-blue); opacity: .6; margin-top: 4px; height: 74px; }
  .address { color: var(--ink-grey); font-size: 15px; line-height: 1.4; font-style: normal; margin-top: 4px; }
</style>
</head>
<body>
<main class="canvas">

  <section class="card card-back" aria-label="Card back">
    <div class="wordmark">brightpath</div>
    <div class="wordmark-sub">MEDIA</div>
    <div class="url">www.brightpath.example</div>
  </section>

  <section class="card card-front" aria-label="Card front">
    <svg class="corner-shapes" viewBox="0 0 620 354" preserveAspectRatio="none" aria-hidden="true">
      <path d="M0 120 L80 120 Q20 200 60 300 L0 300 Z" fill="var(--soft-grey)"/>
      <path d="M620 90 L620 300 L580 300 Q615 190 560 110 Q590 95 620 90 Z" fill="var(--brand-blue)"/>
      <ellipse cx="320" cy="210" rx="280" ry="210" fill="var(--card-white)"/>
    </svg>

    <div class="wordmark">brightpath</div>
    <div class="wordmark-sub">MEDIA</div>

    <div class="contact">
      <div class="person">
        <div class="name">Mara Quinn</div>
        <div class="role">President</div>
        <ul class="details">
          <li><svg viewBox="0 0 16 16"><path d="M3 1h3l1.5 4-2 1.2a9 9 0 0 0 4.3 4.3L11 8.5l4 1.5v3a2 2 0 0 1-2 2A12 12 0 0 1 1 3a2 2 0 0 1 2-2z"/></svg>555 0142 7781</li>
          <li><svg viewBox="0 0 16 16"><path d="M4 1h7v4H4z M1 6h14v7h-3v2H4v-2H1z M5 11v3h6v-3z"/></svg>555 0198 3364</li>
          <li><svg viewBox="0 0 16 16"><path d="M1 3h14v10H1z M2 4l6 5 6-5v-.2H2z" fill-rule="evenodd"/></svg>mara@brightpath.example</li>
        </ul>
      </div>
      <div class="divider"></div>
      <address class="address">1270 Harbor View Road<br>Fairmont, NY 10000</address>
    </div>
  </section>

</main>
</body>
</html>
```